Rack Card for Charter Sail Boat business in SF Bay

We are in need of a rack card design to highlight the business to tourists and locals. 2 sided card 3.86" x 8.39" (full bleed)

We are looking for visually appleaing designs on the front and back but a little more detail on the back.

Use the info provided (text and info) on the website to include the 3 key services (Quick, 1/2 day, fullday) and aspects of the boat, location and other key info for customers (not prices). DO NOT INCLUDE ALL THIS TEXT please pick the elements you would like to fit your design and inform the customer as you would like about the business.

I can also provide photos directly from the video if you think those would fit your design. If video doesn't work on this upload you can view it at the website or facebook page (www.fb.com/tidewrenmarinellc)

Target Market(s)

Tourists and locals to san francisco east bay. 25 - 55 years old. Men and women.

Industry/Entity Type

Entertainment

Colors
0455a3
ec1f27
f3f1f8

Requirements
Must have
• Highlight services, key contact information (email, phone, website site), Visual impact
• 2-sided card - 3.86" x 8.39" (98 x 213 mm)
Nice to have
• facebook link, electric engine(green),

```html
<!DOCTYPE html>
<html lang="en">
<head>
<meta charset="utf-8">
<title>Tidewren Marine Rack Card</title>
<link href="https://fonts.googleapis.com/css2?family=Arvo:wght@400;700&family=Raleway:wght@300;400&family=Noto+Serif:wght@400&family=Arimo:wght@400&display=swap" rel="stylesheet">
<style>
:root{
  --blue:#0455a3;
  --blue-deep:#0a3f86;
  --blue-light:#5fb6ec;
  --red:#ec1f27;
  --paper:#f3f1f8;
  --white:#ffffff;
  --ink:#1b2233;
  --stage:#e9e7ee;
}
*{box-sizing:border-box;margin:0;padding:0}
html,body{width:1200px;height:1000px;overflow:hidden}
body{background:var(--stage);position:relative;font-family:"Arimo",sans-serif}
.card{position:absolute;top:38px;width:433px;height:922px;overflow:hidden;box-shadow:0 6px 18px rgba(0,0,0,.25)}
.card-front{left:130px;background:var(--blue)}
.card-back{left:620px;background:var(--paper)}

/* front */
.hero-photo{position:absolute;left:0;top:0;width:433px;height:300px;background:linear-gradient(180deg,#6f9cc8 0%,#c9d4de 35%,#8d969f 65%,#2c3440 100%)}
.bay-photo{position:absolute;left:170px;top:290px;width:263px;height:520px;background:linear-gradient(90deg,rgba(4,85,163,1) 0%,rgba(4,85,163,.55) 40%,rgba(120,150,175,.6) 100%),linear-gradient(180deg,#9fb1c3 0%,#5d7894 50%,#1e3f6c 100%)}
.swoosh{position:absolute;left:0;width:433px}
.front-title{position:absolute;left:0;top:308px;width:433px;text-align:center;font-family:"Arvo",serif;font-weight:700;font-size:29px;line-height:32px;color:var(--white);letter-spacing:.5px}
.feature{position:absolute;left:26px;width:210px}
.feature-head{display:flex;align-items:center;gap:6px;font-family:"Arvo",serif;font-weight:700;font-size:17px;color:var(--blue-light)}
.feature-text{margin-left:17px;margin-top:3px;font-size:9.4px;line-height:11.6px;color:var(--white)}
.tick{width:11px;height:11px}
.front-foot{position:absolute;left:0;top:770px;width:433px;height:152px}
.brand-disc{position:absolute;left:8px;top:752px;width:138px;height:138px;border-radius:50%;background:var(--white);border:5px solid var(--red);display:flex;align-items:center;justify-content:center;font-family:"Arvo",serif;font-weight:700;font-size:20px;color:var(--blue);text-align:center;line-height:22px}
.contact{position:absolute;font-family:"Arvo",serif;color:var(--ink)}
.contact-phone{font-weight:700;font-size:16px}
.contact-line{font-size:12.5px;line-height:17px}
.social{display:flex;gap:6px;margin-top:6px}
.social span{width:15px;height:15px;border-radius:2px;background:var(--blue)}

/* back */
.back-head{position:absolute;left:0;top:0;width:433px;height:197px;background:var(--blue)}
.back-title{position:absolute;top:22px;width:100%;text-align:center;font-family:"Arvo",serif;font-weight:700;font-size:23px;color:var(--white);letter-spacing:.5px}
.back-intro{position:absolute;left:22px;top:60px;width:392px;font-family:"Raleway",sans-serif;font-weight:300;font-size:13.2px;line-height:18.2px;color:var(--white)}
.red-rule{position:absolute;left:0;top:197px;width:433px;height:4px;background:var(--red)}
.trip-tab{position:absolute;left:126px;top:185px;width:172px;height:38px;background:var(--red);border-radius:5px;font-family:"Arvo",serif;font-weight:700;font-size:24px;line-height:38px;color:var(--white);text-align:center}
.trip-area{position:absolute;left:0;top:201px;width:433px;height:600px;background:linear-gradient(180deg,#f5f4f8 0%,#e6e6ec 60%,#d9dbe3 100%)}
.route-map{position:absolute;width:116px;height:116px;border-radius:50%;border:4px solid var(--blue-deep);box-shadow:0 0 0 2px var(--white);background:radial-gradient(circle at 40% 45%,#b8d0e4 0%,#d9e5d4 55%,#e8e6dc 100%)}
.bridge-photo{background:radial-gradient(circle at 55% 60%,#ffe08a 0%,#f39a2a 30%,#a84f1a 65%,#3b2a2a 100%)}
.trip{position:absolute;width:250px}
.trip-name{font-family:"Arvo",serif;font-weight:700;font-size:18px;color:var(--blue-deep)}
.trip-text{font-family:"Noto Serif",serif;font-size:12.3px;line-height:15.6px;color:var(--ink);margin-top:2px}
.trip-right{text-align:right}
.back-foot{position:absolute;left:0;top:780px;width:433px;height:142px}
.foot-brand{position:absolute;left:20px;top:842px;font-family:"Arvo",serif;font-weight:700;font-size:21px;color:var(--white)}
.foot-contact{position:absolute;left:173px;top:812px;font-family:"Arvo",serif;color:var(--white)}
.foot-note{font-family:"Raleway",sans-serif;font-size:10.5px}
.foot-phone{display:flex;align-items:center;gap:5px;font-weight:700;font-size:15px;margin-top:5px}
.foot-line{font-size:12px;line-height:17px}
.foot-social{position:absolute;left:351px;top:870px;display:flex;gap:6px}
.foot-social span{width:14px;height:14px;border-radius:2px;background:var(--blue-light)}
</style>
</head>
<body>

<section class="card card-front">
  <div class="hero-photo" role="img" aria-label="Sailboat cockpit with canvas dodger moored at a marina under blue sky"></div>
  <div class="bay-photo" role="img" aria-label="View across the bay from the bow of a sailboat toward hills"></div>
  <svg class="swoosh" style="top:262px" height="60" viewBox="0 0 433 60" aria-hidden="true">
    <path d="M0 38 Q200 -8 433 14 L433 60 L0 60 Z" fill="var(--red)"/>
    <path d="M0 52 Q210 6 433 24 L433 60 L0 60 Z" fill="var(--blue)"/>
  </svg>
  <h1 class="front-title">ULTIMATE EAST BAY<br>SAILBOAT CHARTER</h1>

  <div class="feature" style="top:396px">
    <div class="feature-head"><svg class="tick" viewBox="0 0 11 11"><rect x=".5" y=".5" width="10" height="10" fill="none" stroke="var(--blue-light)"/><path d="M2.5 5.5l2 2 4-5" fill="none" stroke="var(--blue-light)" stroke-width="1.5"/></svg>MODERN</div>
    <p class="feature-text">Tidewren has gone completely electric which means no diesel smells, noise or vibration to suffer. New electrics, plumbing, toilets, and deck areas compliment the elegant lines and features of this Harlan Mercer 46 foot cutter rigged sailboat.</p>
  </div>
  <div class="feature" style="top:510px">
    <div class="feature-head"><svg class="tick" viewBox="0 0 11 11"><rect x=".5" y=".5" width="10" height="10" fill="none" stroke="var(--blue-light)"/><path d="M2.5 5.5l2 2 4-5" fill="none" stroke="var(--blue-light)" stroke-width="1.5"/></svg>ENTERTAINING</div>
    <p class="feature-text">Surrounded by the beauty and wonder of the San Francisco Bay you will enjoy the choice of sounds from your source, CD or old school FM! You can take the helm to experience the thrill of sailing Tidewren while we explore Alcatraz and Angel Islands.</p>
  </div>
  <div class="feature" style="top:626px">
    <div class="feature-head"><svg class="tick" viewBox="0 0 11 11"><rect x=".5" y=".5" width="10" height="10" fill="none" stroke="var(--blue-light)"/><path d="M2.5 5.5l2 2 4-5" fill="none" stroke="var(--blue-light)" stroke-width="1.5"/></svg>SAFE</div>
    <p class="feature-text">The safety of everyone aboard is paramount to our business and your enjoyment. We carry aboard everything to make your time aboard safe. Life preservers are provided and available for all including kids sizes. We carry self inflating slim comfortable life jackets.</p>
  </div>

  <svg class="front-foot" viewBox="0 0 433 152" aria-hidden="true">
    <path d="M0 40 Q220 80 433 0 L433 152 L0 152 Z" fill="var(--red)"/>
    <path d="M0 52 Q230 92 433 20 L433 152 L0 152 Z" fill="var(--white)"/>
  </svg>
  <div class="brand-disc">Tidewren<br>Marine</div>
  <div class="contact" style="left:208px;top:832px">
    <div class="contact-phone">+1 (510) 555 WREN (9736)</div>
    <div class="contact-line" style="text-align:right;width:207px">bookings@TidewrenMarine.com</div>
    <div class="contact-line" style="text-align:right;width:207px">www.tidewrenmarine.com</div>
    <div class="social" style="justify-content:flex-end;width:207px"><span></span><span></span><span></span></div>
  </div>
</section>

<section class="card card-back">
  <div class="trip-area"></div>
  <div class="back-head">
    <h2 class="back-title">WHAT IS TIDEWREN?</h2>
    <p class="back-intro">Tidewren is a 50 foot, center cockpit, cutter rigged, mono-hulled, blue water cruising sail boat. She's a nice sized boat with the driving position and main seats at the center of the boat. She has three positions for sails, main (the big one), jib (front sail) and stay-sail (between main and jib). She has a single hull so will lean over as the wind blows.</p>
  </div>
  <div class="red-rule"></div>
  <div class="trip-tab">THE TRIP</div>

  <div class="route-map" style="left:22px;top:225px" role="img" aria-label="Map of a short loop route on the bay"></div>
  <div class="trip" style="left:163px;top:258px">
    <div class="trip-name">2 HOUR BLAST</div>
    <p class="trip-text">Could be a sunset sail, an early morning wake up cruise or a blast out into the bay anytime to find peace, fresh air and amazing views.</p>
  </div>

  <div class="route-map" style="left:294px;top:368px" role="img" aria-label="Map of a half day route across the bay"></div>
  <div class="trip trip-right" style="left:15px;top:384px">
    <div class="trip-name">1/2 DAY FUN</div>
    <p class="trip-text">Could be a sunset sail, an early morning wake up cruise or a blast out into the bay anytime to find peace, fresh air and amazing views.</p>
  </div>

  <div class="route-map" style="left:22px;top:509px" role="img" aria-label="Map of a full circuit route around the bay"></div>
  <div class="trip" style="left:163px;top:526px">
    <div class="trip-name">FULL DAY ADVENTURE</div>
    <p class="trip-text" style="text-align:justify">The day includes a complete circuit of the Bay and lunch at anchor. Actual duration 7-8 hours</p>
  </div>

  <div class="route-map bridge-photo" style="left:294px;top:646px" role="img" aria-label="Sunset behind a suspension bridge over the bay"></div>
  <div class="trip trip-right" style="left:15px;top:642px">
    <div class="trip-name">CUSTOM CRUISE</div>
    <p class="trip-text">You decide and we'll make it happen. When booking online just select the day and start time as normal and then ,record the length of trip you are looking for as text in the comments and we will get into contact with you to sort it out.</p>
  </div>

  <svg class="back-foot" viewBox="0 0 433 142" aria-hidden="true">
    <path d="M0 14 Q216 -10 433 14 L433 142 L0 142 Z" fill="var(--blue)"/>
  </svg>
  <div class="foot-brand">Tidewren<br>Marine</div>
  <div class="foot-contact">
    <div class="foot-note">For more detailed information call or click</div>
    <div class="foot-phone"><svg width="14" height="14" viewBox="0 0 14 14"><circle cx="7" cy="7" r="6.2" fill="none" stroke="var(--white)" stroke-width="1.2"/><path d="M4.6 3.8l1.3-.3.7 1.6-.8.7a5 5 0 0 0 2.2 2.2l.7-.8 1.6.7-.3 1.3c-3 .2-5.6-2.4-5.4-5.4z" fill="var(--white)"/></svg>+1 (510) 555 WREN (9736)</div>
    <div class="foot-line" style="margin-top:5px">bookings@TidewrenMarine.com</div>
    <div class="foot-line">www.tidewrenmarine.com</div>
  </div>
  <div class="foot-social"><span></span><span></span><span></span></div>
</section>

</body>
</html>
```